Dynamic Business Card for Sports Supplements Company

Hi! I'm looking for an awesome business card to match my existing sports supplement company. I have uploaded my current company logo and screenshot of the front page of my website.

I would like to have something dynamic and interesting and utilize the colors in the website - the reds and purples

The business card should be double sided and focus on a unique eye-catching design on the back and include all the relevant company info.

Most importantly, it should say somewhere: "Sign up on our website for a coupon code."

Target Market(s)

Mostly for women gym goers but it shouldn't be too feminine. It should be in keeping with the website design. It should flow and clearly be connected to it

Industry/Entity Type

Business

Contact Information for Business Card

Lorraine K. Vestal
CEO
LVestal@Quorvanexco.com
www.quorvanexco.com
555.417.3820
P.O. Box 47315
Alder Falls, Oregon 00000

Sign up on our website for a coupon code

Font styles to use
Serif
Sans Serif
Other font styles liked:
• Novecento font family and "Quorvanex" is in AR Destine font

Requirements
Must have
• One side should be a bold Quorvanex logo design. Even just the symbol itself may be o.k. (see attached file)

```html
<!DOCTYPE html>
<html lang="en">
<head>
<meta charset="utf-8">
<title>Quorvanex Business Card</title>
<link rel="stylesheet" href="https://fonts.googleapis.com/css2?family=Open+Sans:wght@400;600;800&display=swap">
<style>
  :root {
    --bg: #e9e6e1;
    --card-black: #0d0d0d;
    --card-black-soft: #1c1c1c;
    --brand-red: #e8202a;
    --white: #ffffff;
    --grey-text: #bdbdbd;
  }
  * { margin: 0; padding: 0; box-sizing: border-box; }
  html, body { width: 1200px; height: 950px; overflow: hidden; }
  body {
    background: var(--bg);
    font-family: "Open Sans", Arial, sans-serif;
    display: flex;
    align-items: center;
    justify-content: center;
    gap: 100px;
  }
  .card {
    position: relative;
    width: 400px;
    height: 700px;
    background: linear-gradient(160deg, var(--card-black-soft), var(--card-black) 60%);
    border-radius: 4px;
    overflow: hidden;
    box-shadow: 0 12px 30px rgba(0,0,0,0.25);
  }
  .card-front .chevron { position: absolute; top: 0; left: 0; width: 400px; height: 400px; }
  .contact {
    position: absolute;
    top: 62px;
    right: 40px;
    text-align: right;
    color: var(--white);
  }
  .contact-name {
    font-size: 21px;
    font-weight: 600;
    letter-spacing: 0.5px;
    text-transform: uppercase;
  }
  .contact-title { font-size: 14px; margin-bottom: 26px; }
  .contact-line {
    font-size: 16px;
    line-height: 1.45;
    display: flex;
    justify-content: flex-end;
    align-items: center;
    gap: 7px;
  }
  .contact-line svg { width: 14px; height: 14px; flex: none; }
  .contact-address { margin-bottom: 2px; }

  .brand {
    position: absolute;
    left: 0;
    right: 0;
    text-align: center;
    color: var(--white);
  }
  .brand-name {
    font-weight: 800;
    letter-spacing: 2px;
    text-transform: uppercase;
    line-height: 1;
  }
  .brand-tagline {
    color: var(--grey-text);
    font-weight: 400;
    text-transform: uppercase;
    letter-spacing: 2.5px;
  }
  .card-front .brand { top: 470px; }
  .card-front .brand-name { font-size: 44px; }
  .card-front .brand-tagline { font-size: 12px; margin-top: 6px; }

  .card-back .brand { top: 250px; }
  .brand-mark {
    display: block;
    width: 46px;
    height: 46px;
    margin: 0 auto 26px;
    background: var(--brand-red);
  }
  .card-back .brand-name { font-size: 42px; }
  .card-back .brand-tagline { font-size: 12px; margin-top: 6px; }
  .coupon-note {
    position: absolute;
    bottom: 70px;
    left: 0; right: 0;
    text-align: center;
    color: var(--white);
    font-size: 16px;
  }
</style>
</head>
<body>
  <section class="card card-front">
    <svg class="chevron" viewBox="0 0 400 400" aria-hidden="true">
      <polygon points="0,270 200,360 400,270 400,300 200,390 0,300" fill="var(--white)"/>
      <polygon points="0,0 400,0 400,255 200,345 0,255" fill="var(--brand-red)"/>
    </svg>
    <div class="contact">
      <p class="contact-name">Lorraine K. Vestal</p>
      <p class="contact-title">CEO</p>
      <p class="contact-line contact-address">P.O. Box 47315</p>
      <p class="contact-line contact-address">Alder Falls, Oregon 00000</p>
      <p class="contact-line">
        <svg viewBox="0 0 16 16" aria-hidden="true"><path fill="currentColor" d="M3.5 1.5l2.5 0 1 3.5-1.6 1.2a8 8 0 0 0 4.4 4.4L11 9l3.5 1v2.5c0 1-1 2-2 2A11 11 0 0 1 1.5 3.5c0-1 1-2 2-2z"/></svg>
        555.417.3820
      </p>
      <p class="contact-line">
        <svg viewBox="0 0 16 16" aria-hidden="true"><rect x="1" y="3" width="14" height="10" rx="1" fill="currentColor"/><path d="M1.5 3.5L8 9l6.5-5.5" stroke="var(--brand-red)" stroke-width="1.4" fill="none"/></svg>
        LVestal@Quorvanexco.com
      </p>
      <p class="contact-line">
        <svg viewBox="0 0 16 16" aria-hidden="true"><circle cx="8" cy="8" r="7" fill="currentColor"/><path d="M1 8h14M8 1c-3 3-3 11 0 14M8 1c3 3 3 11 0 14" stroke="var(--brand-red)" stroke-width="1" fill="none"/></svg>
        www.quorvanexco.com
      </p>
    </div>
    <div class="brand">
      <p class="brand-name">Quorvanex</p>
      <p class="brand-tagline">Your Training Companion</p>
    </div>
  </section>

  <section class="card card-back">
    <div class="brand">
      <span class="brand-mark" aria-hidden="true"></span>
      <p class="brand-name">Quorvanex</p>
      <p class="brand-tagline">Your Training Companion</p>
    </div>
    <p class="coupon-note">Sign up on our website for a coupon code</p>
  </section>
</body>
</html>
```